Create a memorable Web Design for real estate branding

we are a Minnepolis brokerage and boutique housing specialist with over 27 years of experience in the Global furnished housing industry, servicing the Greater Los Angeles area. Specializing in “warm environments” we offer a customized approach to satisfying our guests and client’s needs by offering a wide array of options in highly desirable areas. Additionally, Lantern Dwelling Partners offers assistance and expertise to home buyers, sellers and investors.

Industry/Entity Type

Real Estate

Number of Pages Required

1 page

Font styles to use
Serif
Sans Serif
Decorative

```html
<!DOCTYPE html>
<html lang="en">
<head>
<meta charset="utf-8">
<title>Marlowe Crest Realty</title>
<link href="https://fonts.googleapis.com/css2?family=Rubik:wght@400;500;700&family=Lato:wght@400;700&family=Oswald:wght@500&display=swap" rel="stylesheet">
<style>
:root{
  --teal:#1aab8a;
  --teal-dark:#13957a;
  --green:#8dc63f;
  --green-light:#a6d468;
  --ink:#2e2e2e;
  --muted:#666;
  --gray-bg:#f0f0f0;
  --white:#fff;
  --line:#d8d8d8;
}
*{box-sizing:border-box;margin:0;padding:0}
html,body{width:1200px;height:2821px;overflow:hidden}
body{font-family:"Lato",sans-serif;color:var(--ink);position:relative;background:var(--white)}
.abs{position:absolute}
svg{display:block}

/* hero */
.hero{left:0;top:0;width:1200px;height:621px;background:linear-gradient(180deg,#6f9cd6 0%,#9bb7dc 28%,#6a6f78 52%,#3b3a36 70%,#1f4256 100%)}
.brand{left:100px;top:26px;font-family:"Rubik",sans-serif;font-weight:500;font-size:34px;color:var(--green);line-height:1}
.top-contact{top:20px;font-size:13px;color:#222;display:flex;align-items:center;gap:7px}
.nav{top:62px;left:528px;display:flex;align-items:center;gap:30px;font-size:13px;font-weight:700;color:#111;text-transform:uppercase}
.slogan{left:0;font-family:"Oswald",sans-serif;font-size:27px;color:#fff;letter-spacing:.5px;padding-left:100px;display:flex;align-items:center}
.slogan.one{top:422px;height:50px;width:760px;background:rgba(0,0,0,.85);clip-path:polygon(0 0,100% 0,96% 100%,0 100%)}
.slogan.two{top:472px;height:52px;width:1200px;background:linear-gradient(90deg,rgba(0,0,0,.75),rgba(0,0,0,0) 95%)}
.arrow-btn{top:524px;width:36px;height:38px;display:flex;align-items:center;justify-content:center}

/* services */
.services{left:0;top:621px;width:1200px;height:365px;background:var(--teal)}
.section-title{font-family:"Rubik",sans-serif;font-weight:500;text-align:center;width:1200px;left:0}
.services .section-title{top:44px;font-size:36px;color:#fff}
.rule{height:2px;left:480px;width:240px}
.service{width:300px;text-align:center;color:#fff}
.service h3{font-family:"Rubik",sans-serif;font-weight:500;font-size:21px;margin-top:18px}
.service p{font-size:12.5px;line-height:1.45;margin-top:6px;opacity:.92}
.icon-ring{width:114px;height:114px;border-radius:50%;margin:0 auto;background:#fff;padding:6px}
.icon-ring div{width:100%;height:100%;border-radius:50%;background:radial-gradient(circle at 40% 35%,var(--green-light),#6ea82a);display:flex;align-items:center;justify-content:center}
.plus{width:16px;height:16px;background:var(--green);margin:10px auto 0;color:#fff;font-size:14px;line-height:16px;font-weight:700}

/* about */
.about-title{left:100px;top:1052px;font-family:"Rubik",sans-serif;font-size:34px;font-weight:500;color:var(--green)}
.about-title .rest{color:var(--green)}
.about-rule{left:100px;top:1110px;width:610px;height:1px;background:var(--line)}
.about-copy{left:100px;top:1128px;width:612px;font-size:12.2px;line-height:1.85;color:#333}
.pillar{top:1270px;display:flex;gap:16px;width:290px}
.pillar .disc{flex:none;width:60px;height:60px;border-radius:50%;background:var(--teal);display:flex;align-items:center;justify-content:center}
.pillar h4{font-family:"Rubik",sans-serif;font-weight:500;font-size:19px;color:#222}
.pillar p{font-size:12px;line-height:1.6;color:#555;margin-top:4px}
.quick{left:758px;top:1070px;width:343px;height:310px;border:1px solid var(--line);background:#fff}
.quick-tab{left:805px;top:1054px;width:253px;height:44px;background:var(--teal);color:#fff;font-family:"Rubik",sans-serif;font-size:22px;font-weight:500;text-align:center;line-height:44px}
.field{left:778px;width:300px;height:34px;display:flex}
.field .ico{width:30px;display:flex;align-items:flex-start;justify-content:center;padding-top:10px}
.field .box{flex:1;border:1px solid #dcdcdc;font-size:12px;padding:9px 12px;color:#333}
.submit{left:777px;top:1326px;width:96px;height:36px;background:var(--green);color:#123;font-weight:700;font-size:17px;text-align:center;line-height:36px}

/* featured */
.featured{left:0;top:1420px;width:1200px;height:461px;background:var(--gray-bg)}
.two-tone .a{color:var(--teal)}
.two-tone .b{color:var(--green)}
.featured .section-title,.testi-title{font-size:33px;font-weight:500}
.card{top:1557px;width:278px;height:279px;background:#fff;border:1px solid #cfe9e1}
.card .photo{width:278px;height:176px;position:relative}
.price{position:absolute;right:0;bottom:0;background:var(--green);color:#fff;font-weight:700;font-size:16px;padding:5px 10px}
.card h5{font-family:"Rubik",sans-serif;font-weight:400;font-size:19px;color:var(--green);margin:14px 0 0 12px}
.card .loc{font-size:13px;color:#444;margin:3px 0 0 12px}
.card .foot{position:absolute;left:0;bottom:0;width:100%;height:36px;border-top:1px solid #e3e3e3;display:flex;align-items:center;font-size:12.5px;color:#444;padding-left:12px;gap:30px}
.card .foot span{display:flex;align-items:center;gap:6px}
.card .go{position:absolute;right:0;bottom:0;width:36px;height:36px;background:var(--teal);display:flex;align-items:center;justify-content:center}
.hover-cap{position:absolute;left:0;top:52px;width:100%;text-align:center;color:#fff;font-size:17px}

/* testimonials */
.bubble{padding:26px 36px 28px 48px;border-radius:8px;color:#fff;font-weight:700;font-size:15.5px;line-height:1.7}
.bubble .q{position:absolute;font-family:"Rubik",sans-serif;font-size:40px;opacity:.5;line-height:1}
.avatar{border-radius:50%;padding:5px;background:#fff}
.avatar div{width:100%;height:100%;border-radius:50%}
.person b{display:block;font-family:"Rubik",sans-serif;font-weight:500;font-size:17.5px;color:#222}
.person span{font-size:15px;color:#444}
.chev{top:2116px}

/* subscribe */
.city{left:0;top:2374px;width:1200px;height:250px;background:linear-gradient(180deg,#3a3a3a,#6c6c6c 50%,#2a2a2a)}
.sub-box{left:147px;top:2446px;width:963px;height:116px;background:#fff;border-top:6px solid transparent;border-image:repeating-linear-gradient(135deg,#d9483b 0 10px,#fff 10px 18px,#6aa7d8 18px 28px,#fff 28px 36px) 6}
.sub-title{left:236px;top:2480px;font-family:"Rubik",sans-serif;font-weight:500;font-size:20px;color:#222;line-height:1.25}
.sub-title span{display:block;font-weight:400;color:#555}
.social{top:2496px;width:28px;height:28px;border-radius:50%}
.email-in{left:600px;top:2492px;width:282px;height:38px;border:1px solid #ccc;font-size:12.5px;color:#999;padding:11px 12px}
.sub-btn{left:904px;top:2492px;width:134px;height:38px;background:var(--teal);color:#fff;font-weight:700;font-size:14px;line-height:38px;text-align:center}

/* footer */
.footer{left:0;top:2624px;width:1200px;height:166px;background:linear-gradient(90deg,var(--teal-dark),var(--teal) 40%,var(--green) 100%)}
.foot-nav{top:2652px;left:0;width:1200px;text-align:center;color:#fff;font-size:14.5px;word-spacing:4px}
.foot-item{top:2714px;display:flex;gap:12px;color:#fff;font-size:12.5px;line-height:1.6}
.foot-item .circ{width:36px;height:36px;border-radius:50%;border:2px solid #fff;display:flex;align-items:center;justify-content:center;flex:none}
.foot-item b{display:block}
.copy{left:0;top:2790px;width:1200px;height:31px;background:var(--teal-dark);color:#fff;font-size:12px;text-align:center;line-height:31px}
</style>
</head>
<body>

<!-- hero -->
<div class="abs hero" role="img" aria-label="Photo of a modern stone luxury home at dusk with a pool"></div>
<div class="abs brand">Marlowe Crest Realty</div>
<div class="abs top-contact" style="left:738px">
  <svg width="22" height="22" viewBox="0 0 22 22"><circle cx="11" cy="11" r="10" fill="none" stroke="#222" stroke-width="1.6"/><rect x="6" y="7.5" width="10" height="7" fill="#222"/><path d="M6 7.5l5 4 5-4" stroke="#fff" fill="none"/></svg>
  hello@marlowecrestrealty.com
</div>
<div class="abs top-contact" style="left:984px;font-size:14px">
  <svg width="22" height="22" viewBox="0 0 22 22"><circle cx="11" cy="11" r="10" fill="none" stroke="#222" stroke-width="1.6"/><path d="M8 6l2 2.5-1.2 1.5a7 7 0 003.2 3.2l1.5-1.2L16 14l-1.5 2c-4 0-8.5-4.5-8.5-8.5z" fill="#222"/></svg>
  555 204 7781
</div>
<nav class="abs nav">
  <svg width="24" height="22" viewBox="0 0 24 22"><path d="M2 11L12 2l10 9" stroke="var(--teal)" stroke-width="2.5" fill="none"/><rect x="5" y="10" width="14" height="10" fill="var(--teal)"/><rect x="10" y="14" width="4" height="6" fill="#fff"/></svg>
  <span>About Us</span><span>Properties</span><span>Resources</span><span>Testimonials</span><span>Contact Us</span>
</nav>
<div class="abs slogan one">WE ARE A BROKERAGE &amp; BOUTIQUE HOUSING SPECIALIST</div>
<div class="abs slogan two">WITH OVER 27 YEARS OF EXPERIENCE IN GREATER LOS ANGELES AREA</div>
<div class="abs arrow-btn" style="left:100px;background:var(--teal)"><svg width="14" height="20"><path d="M11 2L3 10l8 8" stroke="#fff" stroke-width="2" fill="none"/></svg></div>
<div class="abs arrow-btn" style="left:139px;background:var(--green)"><svg width="14" height="20"><path d="M3 2l8 8-8 8" stroke="#fff" stroke-width="2" fill="none"/></svg></div>

<!-- services -->
<section class="abs services">
  <h2 class="abs section-title">Our Housing Group Offers Assistance And Expertise To</h2>
  <div class="abs rule" style="top:103px;background:rgba(255,255,255,.7)"></div>
  <div class="abs service" style="left:125px;top:136px">
    <div class="icon-ring"><div><svg width="56" height="56" viewBox="0 0 56 56" fill="none" stroke="#fff" stroke-width="3"><path d="M10 26L28 12l18 14"/><rect x="17" y="26" width="22" height="18"/><path d="M6 46h44"/></svg></div></div>
    <h3>Home Sellers</h3>
    <p>Trusted guidance to price, stage<br>and sell your home with ease.</p>
    <div class="plus">+</div>
  </div>
  <div class="abs service" style="left:450px;top:136px">
    <div class="icon-ring"><div><svg width="56" height="56" viewBox="0 0 56 56" fill="none" stroke="#fff" stroke-width="3"><path d="M6 28L24 12l14 12"/><path d="M12 24v20h14"/><circle cx="38" cy="36" r="11"/><text x="38" y="41" font-size="14" text-anchor="middle" fill="#fff" stroke="none" font-family="Lato">$</text></svg></div></div>
    <h3>Home Buyers</h3>
    <p>Find the right home in the right<br>place with our local insight.</p>
    <div class="plus">+</div>
  </div>
  <div class="abs service" style="left:775px;top:136px">
    <div class="icon-ring"><div><svg width="56" height="56" viewBox="0 0 56 56" fill="none" stroke="#fff" stroke-width="3"><path d="M8 26L28 10l20 16"/><rect x="15" y="24" width="26" height="22"/><text x="28" y="41" font-size="16" text-anchor="middle" fill="#fff" stroke="none" font-family="Lato">$</text></svg></div></div>
    <h3>Home Investors</h3>
    <p>Smart picks and market data to<br>grow a strong property portfolio.</p>
    <div class="plus">+</div>
  </div>
</section>

<!-- about -->
<h2 class="abs about-title">About <span class="rest">Marlowe Crest Realty</span></h2>
<div class="abs about-rule"></div>
<p class="abs about-copy">For over twenty-seven years we have helped guests and clients find warm, well furnished homes across Greater Los Angeles. Our team offers a custom approach to every move, with a wide range of options in highly desirable areas. We work closely with buyers, sellers and investors, sharing clear advice, honest pricing and steady support from first visit to final key. Each home we place is chosen with care, so that every stay feels personal, calm and truly comfortable from day one.</p>
<div class="abs pillar" style="left:100px">
  <div class="disc"><svg width="32" height="26" viewBox="0 0 32 26" fill="#fff"><circle cx="16" cy="7" r="5"/><path d="M7 24c0-6 4-9 9-9s9 3 9 9z"/><circle cx="6" cy="10" r="3.5"/><circle cx="26" cy="10" r="3.5"/><path d="M0 22c0-4 2-6 6-6l1 6zM32 22c0-4-2-6-6-6l-1 6z"/></svg></div>
  <div><h4>Who We Are</h4><p>A small, caring team of local<br>housing experts who know<br>each street and every home.</p></div>
</div>
<div class="abs pillar" style="left:400px">
  <div class="disc"><svg width="30" height="30" viewBox="0 0 30 30" fill="none" stroke="#fff" stroke-width="2.4"><circle cx="15" cy="15" r="12"/><circle cx="15" cy="15" r="7"/><circle cx="15" cy="15" r="2" fill="#fff"/><path d="M15 15L27 3"/></svg></div>
  <div><h4>Our Mission</h4><p>To match every client with a<br>warm, welcoming place that<br>truly fits their way of life.</p></div>
</div>

<div class="abs quick"></div>
<div class="abs quick-tab">Quick Contact</div>
<div class="abs field" style="top:1112px"><div class="ico"><svg width="14" height="14"><circle cx="7" cy="4" r="3.5" fill="#555"/><path d="M0 14c0-5 3-6 7-6s7 1 7 6z" fill="#555"/></svg></div><div class="box">Name</div></div>
<div class="abs field" style="top:1158px"><div class="ico"><svg width="14" height="12"><rect width="14" height="10" fill="#555"/><path d="M0 0l7 6 7-6" stroke="#fff" fill="none"/></svg></div><div class="box">Email</div></div>
<div class="abs field" style="top:1206px"><div class="ico"><svg width="14" height="14"><path d="M2 0l3 4-2 2a9 9 0 005 5l2-2 4 3-2 2C6 14 0 8 0 2z" fill="#555"/></svg></div><div class="box">Phone</div></div>
<div class="abs field" style="top:1252px;height:64px"><div class="ico"><svg width="14" height="14" fill="none" stroke="#555" stroke-width="1.5"><rect x="1" y="3" width="10" height="10"/><path d="M5 9l8-8"/></svg></div><div class="box">Message</div></div>
<div class="abs submit">SUBMIT</div>

<!-- featured -->
<section class="abs featured">
  <h2 class="abs section-title two-tone" style="top:30px"><span class="a">Featured</span> <span class="b">Properties</span></h2>
  <div class="abs rule" style="top:90px;left:385px;width:430px;background:#cfcfcf"></div>
</section>
<article class="abs card" style="left:100px">
  <div class="photo" role="img" aria-label="Photo of a bright living room with green walls" style="background:linear-gradient(160deg,#b7c29a,#8e9a6b 55%,#5d5f4d)"><div class="price">$ 1,495,000</div></div>
  <h5>26600 Maple Avenue</h5><div class="loc">Los Angeles Coast</div>
  <div class="foot"><span><svg width="12" height="12" fill="none" stroke="var(--teal)" stroke-width="2"><circle cx="5" cy="5" r="4"/><path d="M8 8l4 4"/></svg>View Details</span><span><svg width="14" height="11"><rect y="2" width="14" height="9" rx="1" fill="var(--teal)"/><circle cx="7" cy="6.5" r="2.5" fill="#fff"/></svg>Photos</span></div>
  <div class="go"><svg width="12" height="18"><path d="M2 2l7 7-7 7" stroke="#fff" stroke-width="2" fill="none"/></svg></div>
</article>
<article class="abs card" style="left:461px">
  <div class="photo" role="img" aria-label="Photo of a modern kitchen with red cabinets" style="background:linear-gradient(160deg,#5a4a48,#3a2e2e 50%,#7a2a26)">
    <div class="hover-cap">Open floor plan kitchen</div>
    <svg class="abs" style="left:124px;top:90px" width="30" height="30" fill="none" stroke="#fff" stroke-width="2.5"><circle cx="12" cy="12" r="9"/><path d="M12 7v10M7 12h10M19 19l8 8"/></svg>
    <div class="price">$ 1,495,000</div></div>
  <h5>26600 Cedar Lane</h5><div class="loc">Los Angeles Coast</div>
  <div class="foot"><span><svg width="12" height="12" fill="none" stroke="var(--teal)" stroke-width="2"><circle cx="5" cy="5" r="4"/><path d="M8 8l4 4"/></svg>View Details</span><span><svg width="14" height="11"><rect y="2" width="14" height="9" rx="1" fill="var(--teal)"/><circle cx="7" cy="6.5" r="2.5" fill="#fff"/></svg>Photos</span></div>
  <div class="go" style="background:var(--green)"><svg width="12" height="18"><path d="M2 2l7 7-7 7" stroke="#fff" stroke-width="2" fill="none"/></svg></div>
</article>
<article class="abs card" style="left:822px">
  <div class="photo" role="img" aria-label="Photo of a grand living room with tall windows" style="background:linear-gradient(160deg,#d8c8a8,#b09570 55%,#6e5840)"><div class="price">$ 1,495,000</div></div>
  <h5>26600 Harbor Drive</h5><div class="loc">Los Angeles Coast</div>
  <div class="foot"><span><svg width="12" height="12" fill="none" stroke="var(--teal)" stroke-width="2"><circle cx="5" cy="5" r="4"/><path d="M8 8l4 4"/></svg>View Details</span><span><svg width="14" height="11"><rect y="2" width="14" height="9" rx="1" fill="var(--teal)"/><circle cx="7" cy="6.5" r="2.5" fill="#fff"/></svg>Photos</span></div>
  <div class="go"><svg width="12" height="18"><path d="M2 2l7 7-7 7" stroke="#fff" stroke-width="2" fill="none"/></svg></div>
</article>

<!-- testimonials -->
<h2 class="abs section-title testi-title two-tone" style="top:1930px;font-family:'Rubik',sans-serif"><span class="a">Client</span> <span class="b">Testimonials</span></h2>
<div class="abs rule" style="top:1993px;left:385px;width:430px;background:#cfcfcf"></div>
<svg class="abs chev" style="left:54px" width="24" height="40"><path d="M20 4L6 20l14 16" stroke="#ccc" stroke-width="2" fill="none"/></svg>
<svg class="abs chev" style="left:1108px" width="24" height="40"><path d="M4 4l14 16L4 36" stroke="#ccc" stroke-width="2" fill="none"/></svg>

<div class="abs bubble" style="left:149px;top:2033px;width:462px;background:var(--teal)">
  <span class="q" style="left:16px;top:12px">&ldquo;</span>
  They found us a lovely furnished home in days. Every step was clear, calm and truly friendly.
  <span class="q" style="right:18px;bottom:0">&rdquo;</span>
</div>
<svg class="abs" style="left:285px;top:2160px" width="40" height="24"><path d="M0 0h40L6 24z" fill="var(--teal)"/></svg>
<div class="abs avatar" style="left:185px;top:2182px;width:100px;height:100px;border:3px solid var(--teal)"><div role="img" aria-label="Portrait of the client" style="background:linear-gradient(160deg,#c9b5a2,#8a7464)"></div></div>
<div class="abs person" style="left:299px;top:2210px"><b>Daniel Ashford</b><span>Customer</span></div>

<div class="abs bubble" style="left:589px;top:2080px;width:462px;background:var(--green-light)">
  <span class="q" style="left:16px;top:12px">&ldquo;</span>
  Great local advice and a warm team. We sold our home fast and at a fair price we loved.
  <span class="q" style="right:18px;bottom:0">&rdquo;</span>
</div>
<svg class="abs" style="left:620px;top:2207px" width="40" height="24"><path d="M0 0h40L34 24z" fill="var(--green-light)"/></svg>
<div class="abs avatar" style="left:617px;top:2234px;width:100px;height:100px;border:3px solid var(--green)"><div role="img" aria-label="Portrait of the client" style="background:linear-gradient(160deg,#d8bfa8,#8a6a52)"></div></div>
<div class="abs person" style="left:732px;top:2264px"><b>Clara Whitmore</b><span>Customer</span></div>

<!-- subscribe -->
<div class="abs city" role="img" aria-label="Black and white photo of a city skyline at dusk with palm trees"></div>
<div class="abs sub-box"></div>
<svg class="abs" style="left:160px;top:2474px" width="64" height="60" fill="none" stroke="#ddd" stroke-width="2"><rect x="2" y="10" width="58" height="40"/><path d="M2 10l29 22 29-22M2 50l22-20M60 50L38 30"/></svg>
<div class="abs sub-title">SUBSCRIBE<span>for Latest News</span></div>
<div class="abs social" style="left:455px;background:#3b5998"></div>
<div class="abs social" style="left:493px;background:#2b9fd9"></div>
<div class="abs social" style="left:531px;background:#d94a38"></div>
<div class="abs email-in">Enter Email Address</div>
<div class="abs sub-btn">SUBSCRIBE</div>

<!-- footer -->
<footer class="abs footer"></footer>
<div class="abs foot-nav">Home / About Us / Properties / Resources / Testimonials / Contact Us</div>
<div class="abs foot-item" style="left:245px">
  <div class="circ"><svg width="14" height="18"><path d="M7 17C3 11 1 8 1 6a6 6 0 0112 0c0 2-2 5-6 11z" fill="none" stroke="#fff" stroke-width="2"/><circle cx="7" cy="6" r="2" fill="#fff"/></svg></div>
  <div><b>Marlowe Crest Realty</b>218 Orchard Way, Suite 4</div>
</div>
<div class="abs foot-item" style="left:518px">
  <div class="circ"><svg width="16" height="16"><path d="M3 1l3 4-2 2a9 9 0 005 5l2-2 4 3-2 2C7 15 1 9 1 3z" fill="#fff"/></svg></div>
  <div><b>Call Us:</b>555-204-7781</div>
</div>
<div class="abs foot-item" style="left:700px">
  <div class="circ"><svg width="16" height="12"><rect width="16" height="12" fill="#fff"/><path d="M0 0l8 6 8-6" stroke="var(--teal)" fill="none"/></svg></div>
  <div><b>Email Us:</b>hello@marlowecrestrealty.com</div>
</div>
<div class="abs copy">Copyright © 2016 Marlowe Crest Realty.  All Rights Reserved</div>

</body>
</html>
```